Automotive eCommerce Business looking for a business card design

Looking for a clean and simple business card design. Our company name is "Brindle Auto" and we are a company specializing in the ecommerce sales of automotive parts, specifically for pick up trucks and large SUVs. Our company colours are red, black, and white.

Feel free to use the logo provided or create a new logo that you seem fit. Looking forward to your creative ideas!

Industry/Entity Type

Automotive

Contact Information for Business Card

We were thinking of a possibly two-sided design featuring just the logo and company name on one side, and personal information on the other side. Single sided designs will be considered as well.

Font styles to use
Serif
Sans Serif
Decorative

Colors
ec1f27
ffffff
000000

Requirements
Must have
• Space for employee's name, title, phone number and email address, along with the company address and website somewhere.

```html
<!DOCTYPE html>
<html lang="en">
<head>
<meta charset="utf-8">
<title>Brindle Auto – Business Card</title>
<link rel="stylesheet" href="https://fonts.googleapis.com/css2?family=Cinzel:wght@500&family=Roboto:wght@400;500&family=Roboto+Condensed:wght@500&display=swap">
<style>
  :root {
    --backdrop: #2b2b2b;
    --paper: #f1f1f1;
    --brand-red: #9b1c20;
    --ink: #4a4a4a;
    --ink-soft: #5a5a5a;
    --white: #ffffff;
  }
  * { margin: 0; padding: 0; box-sizing: border-box; }
  html, body { width: 1200px; height: 960px; overflow: hidden; }
  body {
    background: var(--backdrop);
    position: relative;
    font-family: "Roboto", Arial, sans-serif;
  }
  .card {
    position: absolute;
    width: 600px;
    height: 342px;
    background: var(--paper);
    overflow: hidden;
  }
  .card--front { left: 314px; top: 113px; }
  .card--back { left: 311px; top: 472px; }

  .holder { position: absolute; left: 44px; top: 44px; }
  .holder__name {
    font-family: "Roboto Condensed", Arial, sans-serif;
    font-weight: 500;
    font-size: 21px;
    color: var(--brand-red);
    line-height: 24px;
  }
  .holder__title {
    font-size: 15px;
    font-weight: 500;
    color: var(--ink);
    line-height: 20px;
    margin-top: 2px;
  }

  .address {
    position: absolute; left: 44px; top: 162px;
    font-size: 14.5px; line-height: 19px; color: var(--ink);
  }
  .contacts {
    position: absolute; left: 44px; top: 210px;
    list-style: none;
  }
  .contacts li {
    display: flex; align-items: center;
    height: 19px;
    font-size: 14.5px; color: var(--ink);
  }
  .contacts svg {
    width: 12px; height: 12px;
    margin-right: 11px;
    fill: var(--brand-red);
    flex: none;
  }

  .brand-panel {
    position: absolute; left: 276px; top: 0;
    width: 324px; height: 342px;
    background: var(--brand-red);
    display: flex; align-items: center; justify-content: center;
  }
  .brand-panel__name {
    font-family: "Cinzel", Georgia, serif;
    font-weight: 500;
    font-size: 32px;
    color: var(--white);
  }

  .brand-mark {
    position: absolute; left: 255px; top: 68px;
    width: 90px; height: 90px;
    background: var(--brand-red);
  }
  .brand-name {
    position: absolute; left: 0; width: 100%; top: 228px;
    text-align: center;
    font-family: "Cinzel", Georgia, serif;
    font-weight: 500;
    font-size: 27px;
    color: var(--ink-soft);
  }
  .brand-site {
    position: absolute; left: 0; width: 100%; top: 290px;
    text-align: center;
    font-size: 14px;
    letter-spacing: 5.5px;
    color: var(--ink);
  }
</style>
</head>
<body>

<section class="card card--front">
  <div class="holder">
    <p class="holder__name">ELENA MARSH</p>
    <p class="holder__title">CEO/FOUNDER</p>
  </div>

  <p class="address">1420 Larkspur Road<br>Fairbanks, Alaska 99701</p>

  <ul class="contacts">
    <li><svg viewBox="0 0 12 12"><path d="M2.5 0.5l2 2-1.2 1.5c.8 1.8 2.2 3.2 4 4L8.8 6.8l2.2 2-1.2 2.7C5 11 1 7 .5 2.2z"/></svg>907 555 0142</li>
    <li><svg viewBox="0 0 12 12"><path d="M3 0h6v12H3zM4 1.2v8.3h4V1.2zM5.5 10.2h1v1h-1z"/></svg>907 555 0187</li>
    <li><svg viewBox="0 0 12 12"><path d="M3 0h6v3H3zM0 4h12v5H0zM3 7h6v5H3z"/></svg>907 555 0119</li>
    <li><svg viewBox="0 0 12 12"><path d="M0 2.5h12v7H0zM1 3.3l5 3.4 5-3.4v.9L6 7.6 1 4.2z"/></svg>elena@brindleauto.shop</li>
    <li><svg viewBox="0 0 12 12"><circle cx="6" cy="6" r="6"/></svg>www.brindleauto.shop</li>
  </ul>

  <div class="brand-panel">
    <span class="brand-panel__name">Brindle Auto</span>
  </div>
</section>

<section class="card card--back">
  <div class="brand-mark"></div>
  <p class="brand-name">Brindle Auto Ltd.</p>
  <p class="brand-site">www.brindleauto.shop</p>
</section>

</body>
</html>
```